New Innovative Counselling and psychotherapy Service needs Business Card design

Keep it simple and professional. On one side, just company name and logo (perhaps in all blue) and maybe a tag line.

On other side (all white) my name and Qualifications in centre

Industry/Entity Type

Health And Wellness

Contact Information for Business Card

Dara Whelby
Counsellor & Psychotherapist
BSc (Psychol.), BA, Dip. (Couns. & Psych.), PG.Cert (CBT), FGTrK, ONRE

I will also require Mobile no, Email and web site address of which I'll pass on to final designer.

Font styles to use
Sans Serif

Requirements
Must have
• My Logo Only and please use the colours in logo that is in it.
Should not have
• Any other images

```html
<!DOCTYPE html>
<html lang="en">
<head>
<meta charset="utf-8">
<title>Brightwell Lane – Business Card</title>
<link rel="stylesheet" href="https://fonts.googleapis.com/css2?family=Montserrat:ital,wght@0,300;0,400;0,700;0,800;1,400&display=swap">
<style>
  :root {
    --sky: #4aaee0;
    --sky-light: #e3f1f9;
    --ink: #454545;
    --ink-soft: #5a5a5a;
    --rule: #c9c9c9;
    --paper: #ffffff;
    --backdrop: #eceae6;
  }
  * { box-sizing: border-box; margin: 0; padding: 0; }
  html, body {
    width: 1200px; height: 960px; overflow: hidden;
    background: var(--backdrop);
    font-family: "Montserrat", Arial, sans-serif;
  }
  .sheet {
    width: 1200px; height: 960px;
    display: flex; flex-direction: column; align-items: center; justify-content: center;
    gap: 40px;
  }
  .card {
    position: relative;
    width: 700px; height: 400px;
    overflow: hidden;
    box-shadow: 0 2px 10px rgba(0,0,0,.12);
  }

  /* Front side */
  .card--front { background: var(--sky); color: var(--paper); }
  .front-brand {
    position: absolute; left: 110px; top: 150px;
    display: flex; align-items: center; gap: 26px;
  }
  .front-brand .brand-dot {
    width: 74px; height: 74px; border-radius: 50%; background: var(--paper);
  }
  .front-brand .brand-name {
    font-size: 48px; font-weight: 400; letter-spacing: .5px; color: var(--paper);
  }
  .front-web {
    position: absolute; left: 0; right: 0; top: 262px;
    text-align: center; font-size: 15px; letter-spacing: 2px; padding-left: 120px;
  }

  /* Back side */
  .card--back { background: var(--paper); color: var(--ink); }
  .back-decor {
    position: absolute; left: 400px; top: 190px;
    width: 380px; height: 380px; border-radius: 50%;
    background: var(--sky-light);
  }
  .back-brand {
    position: absolute; right: 44px; top: 56px;
    display: flex; align-items: center; gap: 14px;
  }
  .back-brand .brand-dot {
    width: 40px; height: 40px; border-radius: 50%; background: var(--sky);
  }
  .back-brand .brand-name { font-size: 21px; font-weight: 400; color: var(--ink); }
  .person { position: absolute; left: 64px; top: 54px; }
  .person-name { font-size: 30px; font-weight: 800; color: var(--ink); letter-spacing: .3px; }
  .person-quals {
    margin-top: 8px; font-size: 13.5px; font-style: italic; line-height: 1.8; color: var(--ink-soft);
  }
  .divider {
    position: absolute; left: 64px; top: 244px; width: 64px; height: 1px; background: var(--rule);
  }
  .contact { position: absolute; left: 64px; top: 274px; list-style: none; }
  .contact li {
    display: flex; align-items: center; gap: 12px;
    font-size: 17px; color: var(--ink); height: 30px;
  }
  .contact svg { width: 16px; height: 16px; flex: none; }
</style>
</head>
<body>
<main class="sheet">
  <section class="card card--front" aria-label="Card front">
    <div class="front-brand">
      <span class="brand-dot"></span>
      <span class="brand-name">Brightwell Lane</span>
    </div>
    <p class="front-web">www.brightwelllane.com</p>
  </section>

  <section class="card card--back" aria-label="Card back">
    <div class="back-decor"></div>
    <div class="back-brand">
      <span class="brand-dot"></span>
      <span class="brand-name">Brightwell Lane</span>
    </div>
    <div class="person">
      <h1 class="person-name">Dara Whelby</h1>
      <p class="person-quals">
        Counsellor &amp; Psychotherapist<br>
        BSc (Psychol.)<br>
        BA, Dip. (Couns. &amp; Psych.)<br>
        PG.Cert (CBT), FGTrK, ONRE
      </p>
    </div>
    <div class="divider"></div>
    <ul class="contact">
      <li>
        <svg viewBox="0 0 16 16" aria-hidden="true"><path d="M3.5 1.5l2.5 0 1 3.5-1.6 1.2a8 8 0 0 0 4.4 4.4L11 9l3.5 1v2.5c0 1-1 2-2 2A11 11 0 0 1 1.5 3.5c0-1 1-2 2-2z" fill="var(--sky)"/></svg>
        000 000 0000
      </li>
      <li>
        <svg viewBox="0 0 16 16" aria-hidden="true"><rect x="1" y="3" width="14" height="10" fill="none" stroke="var(--sky)" stroke-width="1.3"/><path d="M1 3l7 6 7-6" fill="none" stroke="var(--sky)" stroke-width="1.3"/></svg>
        dara@brightwelllane.com
      </li>
      <li>
        <svg viewBox="0 0 16 16" aria-hidden="true"><g fill="none" stroke="var(--sky)" stroke-width="1.2"><circle cx="8" cy="8" r="6.5"/><ellipse cx="8" cy="8" rx="3" ry="6.5"/><path d="M1.5 8h13M2.5 4.8h11M2.5 11.2h11"/></g></svg>
        www.brightwelllane.com
      </li>
    </ul>
  </section>
</main>
</body>
</html>
```